New Business Card Design Project LORVANTI-Italy

we are LORVANTI-Italy
our company in the market for 3 years we are luxury cosmetic company and its about time for a facelift :)
i will like to have elegant luxurious and unique business card
that will give the person that get it a unique, luxurious and elegant impression
I'm VERY OPEN FOR NEW IDEAS , even duo i add a few files of things that i see on line and i like them

i add my logo as well
my website is LORVANTI.COM
(if you would like to see the main style that we have)

Target Market(s)

adult that have money :)

Industry/Entity Type

Business

Contact Information for Business Card

Name - Dario Lorvanti
Position - CEO and CO Founder
address - 4817 E Halvern
telephone - 555-384-1926
email - dario@lorvanti.com
fax - 555-384-1926
website - LORVANTI.COM

Colors
000000
959595
fbee3e
ffffff

Requirements
Must have
• big logo in GOLD color
• elegant look
• impressive
Nice to have
• not must but maybe classy pattern background
• not must but maybe emblem
• maybe clear plastic business card
Should not have
• colors
• images

```html
<!DOCTYPE html>
<html lang="en">
<head>
<meta charset="utf-8">
<title>LORVANTI Business Card</title>
<link rel="stylesheet" href="https://fonts.googleapis.com/css2?family=Montserrat:wght@400;500;600&display=swap">
<style>
  :root {
    --canvas: #1b1b1b;
    --card: #1e1e1f;
    --card-edge: #b8892a;
    --gold: #d8ac3e;
    --white: #f4f4f4;
  }
  * { margin: 0; padding: 0; box-sizing: border-box; }
  html, body {
    width: 1200px; height: 833px; overflow: hidden;
    background: var(--canvas);
    font-family: "Montserrat", sans-serif;
  }
  .stage {
    position: relative; width: 1200px; height: 833px;
    display: flex; align-items: center; justify-content: center; gap: 60px;
  }
  .card {
    position: relative; width: 520px; height: 300px;
    background: var(--card);
    border-radius: 3px;
    box-shadow: 0 5px 0 var(--card-edge), 0 18px 30px rgba(0,0,0,.55);
  }
  .brand-dot {
    display: block; border-radius: 50%;
    border: 3px solid var(--gold);
  }
  .brand-name { color: var(--gold); font-weight: 500; }

  /* Front */
  .card-front { display: flex; align-items: center; justify-content: center; }
  .front-mark { display: flex; flex-direction: column; align-items: center; gap: 16px; }
  .front-mark .brand-dot { width: 110px; height: 110px; }
  .front-mark .brand-name { font-size: 30px; letter-spacing: 6px; }

  /* Back */
  .card-back { display: flex; align-items: center; padding: 0 24px 0 26px; }
  .back-brand {
    width: 230px; flex: none;
    display: flex; flex-direction: column; align-items: center; gap: 10px;
  }
  .back-brand .brand-dot { width: 80px; height: 80px; }
  .back-brand .brand-name { font-size: 34px; letter-spacing: 2px; line-height: 1; }
  .brand-rule { width: 228px; height: 2px; background: var(--gold); }
  .divider { width: 1.5px; height: 180px; background: var(--gold); margin: 0 18px 0 16px; flex: none; }
  .contact { color: var(--white); font-size: 13.5px; line-height: 1.32; white-space: nowrap; }
  .contact-name { color: var(--gold); font-weight: 600; font-size: 20px; letter-spacing: .5px; }
  .contact-role { margin-bottom: 12px; }
  .contact-address { margin-bottom: 10px; }
  .contact-list { list-style: none; }
  .contact-list li { display: flex; align-items: center; gap: 8px; }
  .contact-list svg { width: 12px; height: 12px; flex: none; }
</style>
</head>
<body>
<main class="stage">
  <section class="card card-front">
    <div class="front-mark">
      <span class="brand-dot"></span>
      <span class="brand-name">LORVANTI</span>
    </div>
  </section>

  <section class="card card-back">
    <div class="back-brand">
      <span class="brand-dot"></span>
      <span class="brand-name">LORVANTI</span>
      <span class="brand-rule"></span>
    </div>
    <div class="divider"></div>
    <div class="contact">
      <p class="contact-name">Dario Lorvanti</p>
      <p class="contact-role">CEO and Co Founder</p>
      <p class="contact-address">4817 E Halvern<br>Italy</p>
      <ul class="contact-list">
        <li>
          <svg viewBox="0 0 12 12" aria-hidden="true"><path d="M2 1l2.5 0 1 3-1.5 1a6 6 0 0 0 3 3l1-1.5 3 1V10a1 1 0 0 1-1 1A9 9 0 0 1 1 2a1 1 0 0 1 1-1z" fill="var(--gold)"/></svg>
          555-384-1926
        </li>
        <li>
          <svg viewBox="0 0 12 12" aria-hidden="true"><rect x="1" y="4.5" width="10" height="6" fill="none" stroke="var(--gold)"/><rect x="3" y="1" width="6" height="3.5" fill="none" stroke="var(--gold)"/></svg>
          Fax 555-384-1926
        </li>
        <li>
          <svg viewBox="0 0 12 12" aria-hidden="true"><rect x="0.5" y="2.5" width="11" height="7" fill="none" stroke="var(--gold)"/><path d="M.5 2.5L6 7l5.5-4.5" fill="none" stroke="var(--gold)"/></svg>
          dario@lorvanti.com
        </li>
        <li>
          <svg viewBox="0 0 12 12" aria-hidden="true"><circle cx="6" cy="6" r="5.3" fill="none" stroke="var(--gold)"/><ellipse cx="6" cy="6" rx="2.3" ry="5.3" fill="none" stroke="var(--gold)"/><path d="M.7 6h10.6" stroke="var(--gold)"/></svg>
          LORVANTI.COM
        </li>
      </ul>
    </div>
  </section>
</main>
</body>
</html>
```